Redesign This Psychology Website

We would like a slight redesign of this successful psychology (relationship counselling) website:

www.TheKelvaleClinic.com.au

We are updating the website, and we'd like a slight refresh of the design and style.

Please keep to very similar colours, and use the same logo. We're looking for around 10 page templates, however the main one is the home page.

Keep in mind, this website already converts quite well, so we want a new, fresh design in keeping with this one. Please don't bother designing something too extremely different.

thanks :)

Target Market(s)

couples who are looking for relationship counselling. Men and women, 25 - 70, across Australia

Industry/Entity Type

Psychology

Number of Pages Required

5+ page

Font styles to use
Sans Serif

Colors
87cfc6
b7a5cd
ec1f27
ffffff
cee9f5

Requirements
Must have
• a similar look to the current design, just looking for a slight refresh.
• Search bar
• Areas for lots of photos
• same logo
• lots of content areas
Nice to have
• great content areas, where we can display a lot of content and our areas.
Should not have
• no colors like orange, etc.
• should not have a totally different feel.

```html
<!DOCTYPE html>
<html lang="en">
<head>
<meta charset="utf-8">
<title>Sex Therapy Sydney – The Kelvale Clinic</title>
<link href="https://fonts.googleapis.com/css2?family=Mulish:wght@400;600;700;800&display=swap" rel="stylesheet">
<style>
:root{
  --teal:#87cfc6;
  --teal-dark:#4fb3a8;
  --teal-text:#3a9e95;
  --purple:#b7a5cd;
  --purple-dark:#8f78b0;
  --red:#ec1f27;
  --sky:#cee9f5;
  --ink:#333;
  --muted:#666;
  --line:#d6d6d6;
  --bar:#efefef;
  --white:#fff;
}
*{box-sizing:border-box;margin:0;padding:0}
html,body{width:1200px;height:4412px;overflow:hidden}
body{font-family:"Mulish",sans-serif;color:var(--ink);background:var(--white);position:relative;font-size:14px;line-height:1.6}
a{color:inherit;text-decoration:none}
.wrap{width:940px;margin:0 auto;position:relative}

.topbar{height:44px;background:var(--bar);border-bottom:1px solid #e2e2e2;font-size:13px}
.topbar .wrap{display:flex;justify-content:space-between;align-items:center;height:100%}
.topbar ul{display:flex;list-style:none}
.topbar li{padding:0 12px;border-left:1px solid #ccc}
.topbar li:first-child{border-left:0}

.header{height:118px}
.header .wrap{display:flex;align-items:center;height:100%}
.brand{display:flex;align-items:center;gap:12px;width:330px}
.brand-dot{width:40px;height:40px;border-radius:50%;background:var(--teal-dark);flex:none}
.brand-name{font-weight:800;font-size:26px;color:var(--teal-text);line-height:1.1;white-space:nowrap}
.search{width:320px;height:42px;border:1px solid var(--line);border-radius:3px;display:flex;align-items:center;padding:0 12px;gap:8px;color:#999;font-size:13px}
.call{margin-left:auto;text-align:right}
.call small{display:block;color:var(--teal-text);font-size:14px}
.call strong{font-size:26px;color:var(--teal-text);display:flex;align-items:center;gap:8px;font-weight:800}

.nav{height:66px;background:linear-gradient(var(--teal),var(--teal-dark))}
.nav ul{display:flex;list-style:none;height:100%;width:940px;margin:0 auto}
.nav li{flex:auto;display:flex;align-items:center;justify-content:center;text-align:center;color:var(--white);font-weight:700;font-size:14px;line-height:1.2;border-left:1px solid rgba(255,255,255,.5);padding:0 10px}
.nav li:first-child{border-left:0}

.hero{height:322px;background:linear-gradient(100deg,#6c8aa6 0%,#b9a48c 45%,#d8cfc2 70%,#4d6f8e 100%);position:relative}
.hero h1{position:absolute;left:130px;top:168px;color:var(--white);font-size:44px;font-weight:800;letter-spacing:1px}

.content{display:flex;justify-content:space-between;padding-top:50px}
.main{width:610px}
.side{width:305px}

.main h2{font-size:34px;font-weight:600;margin-bottom:14px}
.main p{font-size:13.5px;color:var(--muted);margin-bottom:14px}
.intro-photo{float:right;width:195px;height:195px;border-radius:50%;background:radial-gradient(circle at 40% 40%,#c89a82,#5a4034);margin:-10px 10px 14px 22px}
.clear{clear:both}
.head-red{color:var(--red);font-size:22px;font-weight:600;margin:38px 0 16px;line-height:1.3}
.head-teal{color:var(--teal-text);font-size:24px;font-weight:600;margin:38px 0 16px}
.main strong{color:var(--ink)}

.regions{display:flex;justify-content:space-between;width:560px;margin-top:22px}
.region-col{width:265px}
.region h4{color:var(--teal-text);font-size:15px;font-weight:800;margin:18px 0 12px}
.region:first-child h4{margin-top:0}
.loc{border:1px solid var(--line);padding:14px 16px;height:138px;margin-bottom:14px;font-size:12px;color:var(--muted);line-height:1.55}
.loc b{display:block;color:var(--ink);font-weight:700}
.loc .btn{display:inline-block;margin-top:8px;border:1px solid var(--teal-text);color:var(--teal-text);padding:3px 14px;font-weight:700;font-size:11.5px}

.finder{background:var(--purple);padding:26px 24px 30px;color:var(--white);height:352px}
.finder h3{text-align:center;font-size:24px;line-height:1.2;margin-bottom:20px;font-weight:800}
.finder label{display:block;font-size:12.5px;margin:10px 0 4px}
.finder .field{height:30px;background:var(--white);border-radius:2px;font-size:11px;color:#777;padding:6px 10px}
.finder .go{margin-top:16px;height:36px;background:var(--red);color:var(--white);font-weight:800;text-align:center;line-height:36px;letter-spacing:1px}

.promo{display:flex;height:155px;margin-top:32px;border:1px solid var(--line);box-shadow:0 2px 6px rgba(0,0,0,.08)}
.promo.tall{height:290px}
.promo.dark{height:238px;background:#2d2d33;color:var(--white);border-color:#2d2d33}
.promo-text{width:54%;padding:14px 14px}
.promo h5{font-size:17px;font-weight:800;line-height:1.2;margin-bottom:8px}
.promo p{font-size:10px;color:#888;line-height:1.45}
.promo.dark p{color:#bbb}
.promo .more{display:inline-block;margin-top:10px;background:var(--purple-dark);color:var(--white);font-size:10px;padding:4px 12px;font-weight:700}
.promo-photo{flex:1}

.articles{margin-top:30px}
.article{display:flex;gap:12px;height:146px;margin-bottom:14px;border:1px solid var(--line);padding:10px}
.article-photo{width:140px;flex:none}
.article h6{font-size:14px;font-weight:700;line-height:1.35;color:var(--ink)}
.article span{display:block;color:var(--teal-text);font-size:11px;margin-top:6px}

.footer{position:absolute;left:0;right:0;bottom:80px;height:300px;background:#f4f4f4;border-top:1px solid #e3e3e3}
.footer .wrap{display:flex;padding-top:56px}
.footer .brand{width:310px;align-items:flex-start}
.fcol{width:170px;font-size:13px;color:var(--muted);line-height:1.9}
.fcol h5{color:var(--teal-text);font-size:15px;font-weight:800;margin-bottom:10px;letter-spacing:.5px}
.fcol.contact{width:220px}
.socials{display:flex;gap:8px;margin-top:12px}
.socials i{width:28px;height:28px;border-radius:50%;background:var(--teal-dark);display:block}
.socials i:nth-child(4){background:var(--red)}
.copy{position:absolute;left:0;right:0;bottom:0;height:80px;background:#e9e9e9;text-align:center;line-height:80px;font-size:12px;color:#888}
</style>
</head>
<body>

<div class="topbar">
  <div class="wrap">
    <a>Join Our Associate Program →</a>
    <ul><li>Home</li><li>Cart</li><li>Blog</li><li>Resources</li><li>Contact</li></ul>
  </div>
</div>

<header class="header">
  <div class="wrap">
    <div class="brand">
      <span class="brand-dot"></span>
      <div class="brand-name">The Kelvale Clinic</div>
    </div>
    <div class="search">
      <svg width="14" height="14" viewBox="0 0 14 14"><circle cx="6" cy="6" r="4.5" fill="none" stroke="#999" stroke-width="1.5"/><line x1="9.5" y1="9.5" x2="13" y2="13" stroke="#999" stroke-width="1.5"/></svg>
      Search here
    </div>
    <div class="call">
      <small>Call Us Now</small>
      <strong><svg width="22" height="22" viewBox="0 0 24 24"><path d="M6.6 10.8a15 15 0 0 0 6.6 6.6l2.2-2.2c.3-.3.7-.4 1-.2 1.1.4 2.3.6 3.6.6.6 0 1 .4 1 1V20c0 .6-.4 1-1 1A17 17 0 0 1 3 4c0-.6.4-1 1-1h3.5c.6 0 1 .4 1 1 0 1.3.2 2.5.6 3.6.1.3 0 .7-.2 1z" fill="#ec1f27"/></svg>1300 555 018</strong>
    </div>
  </div>
</header>

<nav class="nav">
  <ul>
    <li>COUNSELLING<br>TYPES</li>
    <li>RELATIONSHIP COUNSELLING<br>LOCATIONS</li>
    <li>SEX THERAPY<br>LOCATIONS</li>
    <li>ABOUT US</li>
    <li>QUIZZES</li>
    <li>FAQ'S</li>
    <li>CONTACT</li>
  </ul>
</nav>

<section class="hero" role="img" aria-label="Photo of a smiling couple sitting close together outdoors">
  <h1>SEX THERAPY SYDNEY</h1>
</section>

<div class="wrap content">
  <main class="main">
    <h2>8 Locations</h2>
    <div class="intro-photo" role="img" aria-label="Round photo of a couple embracing"></div>
    <p>There is not a relationship alive that hasn't occasionally had a struggle with some aspect of their sexual union. Sex and lovemaking can be both the most delectable or disastrous part of our life and our relationship.</p>
    <p>It's because Sex satisfies us in so many ways. We can express our love; we can have great fun; we can enjoy the erotic adventure; we can feel connected; we can revel in ravishing each other and surrendering to the ecstasy of it all.</p>
    <p>When our sex and lovemaking is great, it can provide the glue that keeps us feeling deeply and physically connected with each other, enabling us to better weather many other kinds of relationship storms.</p>
    <div class="clear"></div>
    <p><strong>Sex in a relationship is a huge paradox.</strong></p>
    <p>When it is good and fulfilling, it does play a small but positive role in our relationship (about 15 – 20%). BUT when our sex and lovemaking is NOT satisfying, it becomes an enormous drain and negative role. (from 50 to 75%)</p>

    <h3 class="head-red">You are not the only ones with sexual issues.</h3>
    <p>Research has shown that close to 45% of couples have issues with sexual desire, arousal, orgasm or satisfaction.</p>
    <p>Even though it is easy to assume to the contrary, sexual issues are rarely a simple performance problem with a simple cure. They are usually caused from a combination physical, psychological, and relationship components and can result in much emotional suffering and distress.</p>
    <p>Although sex is a common topic for social jokes, in reality most couples don't really talk much about what they do and don't like with each other, and very few people are actually educated on how to have a healthy lively sex life.</p>

    <h3 class="head-red">Does being in a long term relationship naturally diminish your sexual satisfaction?</h3>
    <p>It is often assumed that if you have been together for a long time, that you can expect to continue to have a satisfying, exciting sex life, but nothing could be further from the truth.</p>
    <p>In reality, the opposite can be true – couples who have been in a committed relationship for 15 years or longer can actually have the best sex of all!</p>

    <h3 class="head-red">Our Sydney Team of Psychologists</h3>
    <p>7 of our Sydney Relationship Psychologists (Carys, Sabine, Marisa, Delia, Lorna, Mirela, and Annika) also specialise in Sex Therapy in addition to couple and marriage counselling.</p>
    <p>Our experience shows us that on many occasions our sex life and our relationships are intricately linked, so having skills and training in both fields as therapists allows us to get the the core of any combined problem and help you create both a better sex life and better relationship.</p>
    <p>As Psychologists, you are also able to receive Medicare rebates for these sessions with us, through Mental Health Care Plans from your GP.</p>
    <p>We have written blog articles on many of the common sexual problems like low libido, differing libidos, difficulty orgasming, premature ejaculation, erectile dysfunction, porn addiction, the truth about performance medication, and maintaining desire.</p>

    <h3 class="head-teal">Our Sydney Sex Therapy Offices:</h3>
    <p>To make any enquiries or bookings with us, please phone 1300 555 018 and our friendly receptionists will help you. Sex Therapy (and Couple relationship) sessions are 50 mins</p>
    <p>Cost: $160 -$175 for after-hours sessions or for all sessions at CBD locations)<br>Private Health Insurance Rebates apply, and Medicare Rebates may apply.<br>(please check for details)</p>

    <h3 class="head-teal">Relationship Counselling Sydney</h3>
    <div class="regions">
      <div class="region-col">
        <div class="region">
          <h4>SYDNEY CBD</h4>
          <div class="loc"><b>SYDNEY CBD (GEORGE ST)</b>Suite 410, Level 5,<br>212 Harbour St<br>Sydney 2000<br><span class="btn">See Our Psychologists</span></div>
          <div class="loc"><b>SYDNEY CBD (PITT ST)</b>Suite 302, Level 3,<br>88 Ferris St<br>Sydney 2000<br><span class="btn">See Our Psychologists</span></div>
        </div>
        <div class="region">
          <h4>SYDNEY INNER WEST</h4>
          <div class="loc"><b>GLEBE</b>47 Larkin Road<br>Glebe 2037<br><span class="btn">See Our Psychologists</span></div>
          <div class="loc"><b>FIVE DOCK</b>Unit 1<br>18 Calder Rd<br>Five Dock 2046<br><span class="btn">See Our Psychologists</span></div>
          <div class="loc"><b>DULWICH HILL</b>9 Wrenfield Ave<br>Dulwich Hill 2203<br><span class="btn">See Our Psychologists</span></div>
        </div>
        <div class="region">
          <h4>SYDNEY WEST</h4>
          <div class="loc"><b>RIVERSTONE</b>Riverstone Family Health Centre<br>6 Ashgrove Parade Riverstone 2765<br><span class="btn">See Our Psychologists</span></div>
          <div class="loc"><b>PARRAMATTA</b>Level 2, 31 Bellamy Street<br>Parramatta 2151<br><span class="btn">See Our Psychologists</span></div>
          <div class="loc"><b>PENRITH</b>64 Tulloch Street Penrith 2750<br><span class="btn">See Our Psychologists</span></div>
          <div class="loc"><b>WINDSOR DOWNS (LOWER)</b>12 Merriot Lane Windsor Downs 2756<br><span class="btn">See Our Psychologists</span></div>
        </div>
      </div>
      <div class="region-col">
        <div class="region">
          <h4>SYDNEY SOUTH</h4>
          <div class="loc"><b>GREEN SQUARE (ROSEBERY)</b>Suite B2, Level 1,<br>14 Dunmore Ave<br>Rosebery 2018<br><span class="btn">See Our Psychologists</span></div>
          <div class="loc"><b>CARINGBAH</b>Suites 2-4, 150 Eastway<br>Caringbah 2229<br><span class="btn">See Our Psychologists</span></div>
        </div>
        <div class="region">
          <h4>SYDNEY NORTH</h4>
          <div class="loc"><b>MOSMAN (MILITARY RD)</b>Harbourside Medical Rooms<br>316 Military Rd Mosman 2088<br><span class="btn">See Our Psychologists</span></div>
          <div class="loc"><b>MOSMAN (COWLES RD)</b>Suite 2, 41 Cowles Rd<br>Mosman 2088<br><span class="btn">See Our Psychologists</span></div>
          <div class="loc"><b>CROWS NEST</b>Suite 105, 27 Alexander St<br>Crows Nest 2065<br><span class="btn">See Our Psychologists</span></div>
          <div class="loc"><b>MONA VALE</b>22 Bramley Rd Mona Vale 2103<br><span class="btn">See Our Psychologists</span></div>
        </div>
        <div class="region">
          <h4>SYDNEY EAST</h4>
          <div class="loc"><b>RANDWICK</b>Suite 3, 58 Avoca St<br>Randwick 2031<br><span class="btn">See Our Psychologists</span></div>
          <div class="loc"><b>BONDI JUNCTION</b>Level 4, 19 Ellery Place<br>Bondi Junction 2022<br><span class="btn">See Our Psychologists</span></div>
        </div>
      </div>
    </div>
  </main>

  <aside class="side">
    <div class="finder">
      <h3>Find Our Psychologist<br>Near You</h3>
      <label>Type of Counselling</label><div class="field">Select</div>
      <label>Location</label><div class="field"></div>
      <label>Postcode</label><div class="field"></div>
      <div class="go">SEARCH</div>
    </div>

    <div class="promo">
      <div class="promo-text"><h5>Rebates Available</h5><p>Many clients can claim part of each session back through Medicare or private cover.</p><span class="more">Learn More</span></div>
      <div class="promo-photo" role="img" aria-label="Photo of a couple talking" style="background:linear-gradient(135deg,#e8d6cc,#b28b78)"></div>
    </div>

    <div class="promo tall">
      <div class="promo-text"><h5>GP Referral Info</h5><p>Ask your GP about a mental health care plan before your first visit with us.</p><span class="more">Learn More</span></div>
      <div class="promo-photo" role="img" aria-label="Photo of a smiling doctor with a stethoscope" style="background:linear-gradient(160deg,#eef3f6,#c5d3dd)"></div>
    </div>

    <div class="promo dark">
      <div class="promo-text"><h5>Anxiety and Depression</h5><p>Support for low mood, worry and stress that affects you and your partner.</p><span class="more">Learn More</span></div>
      <div class="promo-photo" role="img" aria-label="Photo of a person sitting alone looking down" style="background:linear-gradient(160deg,#5a5a62,#1f1f24)"></div>
    </div>

    <div class="articles">
      <div class="article"><div class="article-photo" role="img" aria-label="Photo of two hands touching" style="background:linear-gradient(135deg,#d9b9a0,#8a6650)"></div><div><h6>What can I do if I'm living with a Narcissist?</h6><span>Read More</span></div></div>
      <div class="article"><div class="article-photo" role="img" aria-label="Photo of a woman looking upset" style="background:linear-gradient(135deg,#c8b3a6,#6f5a50)"></div><div><h6>Are You Living With a Stepmother?</h6><span>Read More</span></div></div>
      <div class="article"><div class="article-photo" role="img" aria-label="Photo of a couple turned away from each other" style="background:linear-gradient(135deg,#9aa5ae,#4d5660)"></div><div><h6>Did Your Relationship Start on Rocky Ground?</h6><span>Read More</span></div></div>
      <div class="article"><div class="article-photo" role="img" aria-label="Photo of a couple in conversation" style="background:linear-gradient(135deg,#d8c7b8,#9b806c)"></div><div><h6>Why am I with a Narcissist?</h6><span>Read More</span></div></div>
      <div class="article"><div class="article-photo" role="img" aria-label="Photo of a couple sitting on a couch" style="background:linear-gradient(135deg,#e2d4c4,#a88f74)"></div><div><h6>Letter for a Partner Doubtful About Relationship Counselling</h6><span>Read More</span></div></div>
      <div class="article"><div class="article-photo" role="img" aria-label="Photo of a couple holding hands" style="background:linear-gradient(135deg,#d1a98c,#7d5740)"></div><div><h6>What Are You Like in a Relationship?</h6><span>Read More</span></div></div>
      <div class="article"><div class="article-photo" role="img" aria-label="Photo of a woman in thought" style="background:linear-gradient(135deg,#6f6a70,#2f2b30)"></div><div><h6>How Do I Know If I'm With a Narcissist?</h6><span>Read More</span></div></div>
      <div class="article"><div class="article-photo" role="img" aria-label="Photo of a couple laughing together" style="background:linear-gradient(135deg,#e0b59a,#b06a4c)"></div><div><h6>Do You Wonder Why You and Your Partner Are Together?</h6><span>Read More</span></div></div>
      <div class="article"><div class="article-photo" role="img" aria-label="Photo of a couple at a desk" style="background:linear-gradient(135deg,#b7aba4,#6b5f58)"></div><div><h6>Is Your Pursuit of Success Sabotaging Your Relationships That Matter Most?</h6><span>Read More</span></div></div>
    </div>
  </aside>
</div>

<footer class="footer">
  <div class="wrap">
    <div class="brand">
      <span class="brand-dot"></span>
      <div class="brand-name">The Kelvale Clinic</div>
    </div>
    <div class="fcol"><h5>QUICK LINKS</h5>Home<br>About Us<br>Our Blogs<br>Shop Cart<br>Contact Us</div>
    <div class="fcol"><h5>RESOURCES</h5>Counselling Type<br>Sex Therapy<br>Quizzes<br>FAQ<br>Relationship Counselling</div>
    <div class="fcol contact"><h5>CONTACT US</h5>240 Lakeview Drive Suite 12<br>1300 555 018<br>Email: info@kelvaleclinic.com.au
      <div class="socials"><i></i><i></i><i></i><i></i></div>
    </div>
  </div>
</footer>
<div class="copy">© 2017 The Kelvale Clinic. All right reserved</div>

</body>
</html>
```